CopperWanderer Stretching and Strength

We need a application design for a our first IOS application. the goal of the application is to categorize stretching and strength routines for triathlon.

We would like to see designs that use the color orange.

The design of the application should be compliant with the last version of the IOS Mobile.

For this first design we need the folowing pages:

1- Sign up
2- Log in
3- Home
4- View Exercises
5- Do it
6- Profile

The description of each page is in the attached document.

We need a logo design for the application. The logo should express that mission of the application that is for stretch and strength training for Triathlon.

We will use https://pellavokit.example to develop the application, if you have any experience of the limitation that this technology have it will be a plus.

If you have any question please feel free to contact us.

Reason: We will extend the deadline to be sure that we select the best design from all of you. we will take the final decision next Tuesday.

Target Market(s)

The market for my aplicación is the Running a Triathlon world.

Logo Text

CopperWanderer

Font styles to use
Serif

Colors
f37122
ffffff
dcdcdc

Requirements
Must have
• In some future we will add more features in the menu. We should considere it for the design.
• The designs should include all the screens in the power point.

```html
<!DOCTYPE html>
<html lang="en">
<head>
<meta charset="utf-8">
<title>Strength Exercise – Filter</title>
<link href="https://fonts.googleapis.com/css2?family=Roboto:wght@300;400;500&display=swap" rel="stylesheet">
<style>
:root{
  --bg:#d6e3ef;
  --orange:#f37122;
  --white:#ffffff;
  --grey:#dcdcdc;
  --sheet:#eceff3;
  --text:#444a50;
  --muted:#6b7076;
  --tag-teal:#1fb4c9;
  --tag-pink:#d9479a;
  --tag-purple:#6c3fd6;
  --tag-yellow:#e8b31b;
  --scrim:rgba(0,0,0,.62);
}
*{margin:0;padding:0;box-sizing:border-box}
html,body{width:1200px;height:1200px;overflow:hidden;background:var(--bg);font-family:'Roboto',sans-serif}
.screen{position:absolute;left:269px;top:11px;width:552px;height:982px;transform:scale(1.2);transform-origin:0 0;background:#f4f4f4;overflow:hidden}
.abs{position:absolute}
.status-bar{left:0;top:0;width:552px;height:40px;background:var(--orange);color:var(--white);font-size:16px;font-weight:300}
.status-bar .carrier{left:8px;top:12px}
.status-bar .clock{left:0;width:552px;text-align:center;top:12px}
.status-bar .battery{right:10px;top:12px;display:flex;align-items:center;gap:6px}
.battery-cell{width:34px;height:13px;border:1px solid var(--white);border-radius:2px;padding:1px}
.battery-cell span{display:block;height:100%;background:var(--white)}
.app-bar{left:0;top:40px;width:552px;height:60px;background:var(--orange)}
.app-bar .title{width:552px;text-align:center;top:17px;color:var(--white);font-size:22px;font-weight:500;letter-spacing:.2px}
.menu-icon{left:12px;top:21px}
.filter-icon{right:12px;top:17px}
.search{left:0;top:100px;width:552px;height:46px;background:#fbfbfb;box-shadow:0 2px 3px rgba(0,0,0,.12)}
.search .placeholder{left:46px;top:13px;font-size:17px;color:#8a8f95;font-weight:300}
.search svg{left:16px;top:14px}
.card{left:14px;width:524px;height:140px;background:var(--white);box-shadow:0 1px 3px rgba(0,0,0,.15)}
.thumb{left:10px;top:18px;width:80px;height:76px}
.thumb-a{background:linear-gradient(135deg,#9bb46c,#566a3a 60%,#2f3a2a)}
.thumb-b{background:linear-gradient(160deg,#d9c7b5,#b08d76 55%,#7b5c4c)}
.thumb-c{background:linear-gradient(150deg,#cfc5bb,#8c7b70)}
.card-title{left:106px;top:14px;font-size:18px;color:#333}
.tags{left:106px;top:42px;display:flex;gap:7px}
.tag{height:15px;border-radius:8px;padding:0 12px;font-size:9px;line-height:15px;color:var(--white)}
.t-teal{background:var(--tag-teal)}.t-pink{background:var(--tag-pink)}.t-purple{background:var(--tag-purple)}.t-yellow{background:var(--tag-yellow)}
.card-text{left:106px;top:66px;width:410px;font-size:14px;line-height:22px;color:var(--muted);font-weight:300}
.meta{left:106px;top:113px;font-size:12.5px;color:var(--muted);font-weight:300}
.meta b{color:var(--orange);font-weight:400}
.meta .gap{display:inline-block;width:22px}
.scrim{left:0;top:0;width:552px;height:504px;background:var(--scrim)}
.sheet{left:0;top:504px;width:552px;height:478px;background:var(--sheet);color:var(--text)}
.sheet h2{position:absolute;width:552px;text-align:center;top:24px;font-size:25px;font-weight:400;color:#3a3f44}
.label{left:24px;font-size:20px;color:#3a3f44}
.opt{display:flex;align-items:center;gap:15px;font-size:20px;color:var(--text);font-weight:300}
.box{width:22px;height:22px;border:1.5px solid #9da2a8;background:var(--white);display:block}
.box.on{border-color:var(--orange)}
.apply{left:37px;top:393px;width:476px;height:60px;border-radius:30px;background:var(--orange);color:var(--white);font-size:21px;font-weight:500;text-align:center;line-height:60px;box-shadow:0 3px 5px rgba(0,0,0,.2)}
</style>
</head>
<body>
<div class="screen">
  <div class="abs status-bar">
    <div class="abs carrier">●●●○○ BELL</div>
    <div class="abs clock">4:21 PM</div>
    <div class="abs battery">100% <div class="battery-cell"><span></span></div></div>
  </div>
  <div class="abs app-bar">
    <svg class="abs menu-icon" width="26" height="18" viewBox="0 0 26 18"><path d="M0 2h26M0 9h26M0 16h26" stroke="#fff" stroke-width="2.4"/></svg>
    <div class="abs title">STRENGTH EXERCISE</div>
    <svg class="abs filter-icon" width="24" height="24" viewBox="0 0 24 24"><path d="M1 2h22l-8.5 10v10l-5-3V12z" fill="#fff"/></svg>
  </div>
  <div class="abs search">
    <svg class="abs" width="18" height="18" viewBox="0 0 18 18"><circle cx="7.5" cy="7.5" r="6" fill="none" stroke="#333" stroke-width="1.8"/><path d="M12 12l5 5" stroke="#333" stroke-width="1.8"/></svg>
    <div class="abs placeholder">Search here...</div>
  </div>

  <div class="abs card" style="top:158px">
    <div class="abs thumb thumb-a" role="img" aria-label="Photo of a group doing outdoor stretches"></div>
    <div class="abs card-title">Lorem ipsum dolor sit amet</div>
    <div class="abs tags"><span class="tag t-teal">Flexibility</span><span class="tag t-pink">Leg</span><span class="tag t-purple">Pain Relief</span></div>
    <div class="abs card-text">Lorem ipsum dolor sit amet, consectetur adipiscing elit. Etiam vitae eros efficitur...</div>
    <div class="abs meta"><b>Time:</b> 5:32 min<span class="gap"></span><b>Level:</b> Moderate</div>
  </div>
  <div class="abs card" style="top:306px">
    <div class="abs thumb thumb-b" role="img" aria-label="Photo of a person doing a plank on a mat"></div>
    <div class="abs card-title">Lorem ipsum dolor sit amet</div>
    <div class="abs tags"><span class="tag t-teal">Flexibility</span><span class="tag t-pink">Leg</span><span class="tag t-yellow">Shoulder</span></div>
    <div class="abs card-text">Lorem ipsum dolor sit amet, consectetur adipiscing elit. Etiam vitae eros efficitur...</div>
    <div class="abs meta"><b>Time:</b> 4:25 min<span class="gap"></span><b>Level:</b> Easy</div>
  </div>
  <div class="abs card" style="top:455px">
    <div class="abs thumb thumb-c" role="img" aria-label="Photo of a person stretching on the floor"></div>
    <div class="abs card-title">Lorem ipsum dolor sit amet</div>
    <div class="abs tags"><span class="tag t-teal">Flexibility</span><span class="tag t-purple">Pain Relief</span></div>
  </div>

  <div class="abs scrim"></div>

  <div class="abs sheet">
    <h2>Filter</h2>
    <div class="abs label" style="top:95px">Tags:</div>
    <div class="abs opt" style="left:103px;top:95px"><span class="box on"><svg width="19" height="19" viewBox="0 0 19 19"><path d="M4 10l3.5 3.5L15 5" fill="none" stroke="#f37122" stroke-width="1.5"/></svg></span>Flexibility</div>
    <div class="abs opt" style="left:253px;top:97px"><span class="box"></span>Pain Relief</div>
    <div class="abs opt" style="left:415px;top:97px"><span class="box on"><svg width="19" height="19" viewBox="0 0 19 19"><path d="M4 10l3.5 3.5L15 5" fill="none" stroke="#f37122" stroke-width="1.5"/></svg></span>Shoulder</div>
    <div class="abs opt" style="left:103px;top:134px"><span class="box"></span>Leg</div>

    <div class="abs label" style="top:192px">Sport:</div>
    <div class="abs opt" style="left:103px;top:192px"><span class="box on"><svg width="19" height="19" viewBox="0 0 19 19"><path d="M4 10l3.5 3.5L15 5" fill="none" stroke="#f37122" stroke-width="1.5"/></svg></span>Running</div>
    <div class="abs opt" style="left:241px;top:194px"><span class="box"></span>Bike</div>
    <div class="abs opt" style="left:346px;top:192px"><span class="box on"><svg width="19" height="19" viewBox="0 0 19 19"><path d="M4 10l3.5 3.5L15 5" fill="none" stroke="#f37122" stroke-width="1.5"/></svg></span>Swimming</div>

    <div class="abs label" style="top:249px">Time:</div>
    <div class="abs opt" style="left:103px;top:250px"><span class="box on"><svg width="19" height="19" viewBox="0 0 19 19"><path d="M4 10l3.5 3.5L15 5" fill="none" stroke="#f37122" stroke-width="1.5"/></svg></span>Approximate time of exercise or routine.</div>

    <div class="abs label" style="top:307px">Level:</div>
    <div class="abs opt" style="left:103px;top:308px"><span class="box on"><svg width="19" height="19" viewBox="0 0 19 19"><path d="M4 10l3.5 3.5L15 5" fill="none" stroke="#f37122" stroke-width="1.5"/></svg></span>Easy</div>
    <div class="abs opt" style="left:212px;top:310px"><span class="box on"><svg width="19" height="19" viewBox="0 0 19 19"><path d="M4 10l3.5 3.5L15 5" fill="none" stroke="#f37122" stroke-width="1.5"/></svg></span>Moderate</div>
    <div class="abs opt" style="left:363px;top:310px"><span class="box"></span>Advanced</div>

    <div class="abs apply">APPLY FILTER</div>
  </div>
</div>
</body>
</html>
```